Stationery Design Project

We need a stationery design for our Norwegian trucking company. We have existed for about 15 years and our 12 drivers uses relatively new vehicles to transport goods around in northern Norway. Long distance routes with fresh fish og food transport is our main operations.

We have already made alogo that's printed on our trucks. The logo and a picture of our trucks is attached. I think the logo i crappy, but since its already in use, changing it is not an option in this round. Still using a better colour scheme in the overall stationery and more interesting fonts is possible (altso in the logo).

Company details:
Name: Kjelvraket AS
Organisation nr 873 615 309
Post adress: 8642 Raudvik

I like minimalism and simplicity. I am avalibly for questions in normal GMT working hours either here or on mail: ivar@fjordlast.no

Reason: Hi. Im extending the deadline because I needed some time to find a vector file of our logo. Sorry for the inconvenience

Hi, and thanks for all your interest in the project. Some updates:

-          I have decided to commit to using one of the designs. Some designer will get the payment.

-          I have extended the deadline with 24 hours since I needed some time to find our firms vector logo (a slow Swedish man was holding me up)

-          We will not choose a design before the deadline. No need to rush.

-          We have received a lot of great design and think there is a need to specified the product we want to make:

o   Business Card for all our employers. I just need the design and will duplicate with the correct numbers and name myself. The information on should be: Logo, employer’s name, Phone number, email, website, Postal number and address. Use this as a template: logo, Leif Brattvoll, 47382066, Leif@fjordlast.no,, fjordlast.no, 8642 Raudvik. The order and placement of the information is your creative decision.

o   Stickers to put on the goods we travel. On the sticker the should be the following information: Logo, phone number, Tekst and link: Fraktæ av Kjelvraket. Ke du syns? Fjordlast.no/tilbakemelding (this means: Handled by Kjelvraket. What do you think Fjordlast.no/feedback -à the link will be a feedback form). The placement the information and size is your creative decision with some stings: we have been thinking of using Drukko for printing and see that a size about 6x6 cm, 8x5 or something like that. (with 3000 copies our budget is 200 punds). Any suggestions of other suppliers are welcome. Drukko price calculator http://www.drukkolabelhouse.co.uk/digital-litho-printing/printing-labels-tags/stickers/

o   Letterhead with logo, address, phone number and organizational number.

o   Envelopes with logo,address, phone number and organizational number.

Have a nice day.

 

 

• Using the blue colour in the logo and using a similar graphic approch.

```html
<!DOCTYPE html>
<html lang="no">
<head>
<meta charset="utf-8">
<title>Kjelvraket – visittkort</title>
<link rel="stylesheet" href="https://fonts.googleapis.com/css2?family=Open+Sans:wght@400;600;700&display=swap">
<style>
  :root {
    --stage: #c9ccd0;
    --white: #ffffff;
    --navy: #0b4ea2;
    --blue: #0a72bb;
    --band-blue: #1876c0;
    --ink: #222222;
    --rule: #9a9a9a;
    --radius: 16px;
  }
  * { box-sizing: border-box; margin: 0; padding: 0; }
  html, body { width: 1200px; height: 751px; overflow: hidden; }
  body {
    background: var(--stage);
    font-family: "Open Sans", Arial, sans-serif;
    position: relative;
  }
  .card {
    position: absolute;
    width: 524px;
    height: 299px;
    border-radius: var(--radius);
    overflow: hidden;
  }
  .card--front { left: 64px; top: 52px; background: var(--white); border: 1px solid #bbb; }
  .card--navy  { left: 620px; top: 52px; background: var(--navy); }
  .card--white { left: 64px; top: 393px; background: var(--white); border: 1px solid #bbb; }
  .card--blue  { left: 620px; top: 393px; background: var(--blue); }

  .wordmark {
    position: absolute;
    left: 0; right: 0;
    display: flex;
    align-items: center;
    justify-content: center;
    gap: 14px;
    font-weight: 700;
    font-size: 50px;
    letter-spacing: -0.5px;
  }
  .wordmark__dot { width: 28px; height: 28px; border-radius: 50%; }
  .card--front .wordmark { top: 92px; color: var(--navy); }
  .card--front .wordmark__dot { background: var(--navy); }
  .card--navy .wordmark, .card--blue .wordmark { top: 125px; color: var(--white); }
  .card--navy .wordmark__dot, .card--blue .wordmark__dot { background: var(--white); }
  .card--white .wordmark { top: 125px; color: var(--navy); }
  .card--white .wordmark__dot { background: var(--navy); }

  .website {
    position: absolute;
    left: 0; right: 0;
    text-align: center;
    font-size: 17px;
    letter-spacing: 3.5px;
  }
  .card--navy .website, .card--blue .website { top: 248px; color: var(--white); }
  .card--white .website { top: 248px; color: var(--ink); }

  .contact-name {
    position: absolute;
    right: 296px; top: 170px;
    text-align: right;
    color: var(--navy);
  }
  .contact-name strong { display: block; font-size: 18px; font-weight: 700; }
  .contact-name span { display: block; margin-top: 4px; font-size: 15px; color: var(--ink); }
  .contact-divider {
    position: absolute;
    left: 242px; top: 157px;
    width: 1px; height: 74px;
    background: var(--rule);
  }
  .contact-list {
    position: absolute;
    left: 254px; top: 161px;
    list-style: none;
    font-size: 15px;
    line-height: 23px;
    color: var(--ink);
  }
  .contact-list .label { color: var(--band-blue); }
  .icon { display: inline-block; vertical-align: -1px; margin-right: 4px; }

  .band { position: absolute; left: 0; bottom: 0; width: 524px; height: 42px; }
  .band__url {
    position: absolute;
    left: 272px; bottom: 8px;
    color: var(--white);
    font-size: 16px;
    letter-spacing: 3.5px;
  }
</style>
</head>
<body>

  <section class="card card--front" aria-label="Visittkort forside">
    <div class="wordmark"><span class="wordmark__dot"></span>Kjelvraket</div>

    <div class="contact-name">
      <strong>Leif Brattvoll</strong>
      <span>
        <svg class="icon" width="12" height="10" viewBox="0 0 12 10" aria-hidden="true"><path d="M1 5 6 1l5 4v4H1z" fill="var(--band-blue)"/></svg>8642 Raudvik
      </span>
    </div>
    <div class="contact-divider"></div>
    <ul class="contact-list">
      <li><svg class="icon" width="11" height="11" viewBox="0 0 12 12" aria-hidden="true"><circle cx="6" cy="6" r="5.2" fill="none" stroke="var(--band-blue)" stroke-width="1.3"/><path d="M4 3.5c0 2.6 1.6 4.6 4 5l.6-1.3-1.4-.7-.6.7C5.7 6.6 5.2 5.9 5 5l.7-.5L5.1 3z" fill="var(--band-blue)"/></svg>47382066</li>
      <li><span class="label">Org nr</span> 873 615 309</li>
      <li><svg class="icon" width="11" height="9" viewBox="0 0 12 9" aria-hidden="true"><rect x="0.5" y="0.5" width="11" height="8" rx="1" fill="var(--band-blue)"/><path d="M1 1l5 4 5-4" fill="none" stroke="#fff" stroke-width="1"/></svg>Leif@fjordlast.no</li>
    </ul>

    <svg class="band" viewBox="0 0 524 42" aria-hidden="true">
      <polygon points="0,0 236,0 226,10 0,10" fill="var(--navy)"/>
      <polygon points="238,0 524,0 524,42 0,42 0,22 218,22" fill="var(--band-blue)"/>
    </svg>
    <div class="band__url">www.fjordlast.no</div>
  </section>

  <section class="card card--navy" aria-label="Visittkort bakside, mørk blå">
    <div class="wordmark"><span class="wordmark__dot"></span>Kjelvraket</div>
    <div class="website">www.fjordlast.no</div>
  </section>

  <section class="card card--white" aria-label="Visittkort bakside, hvit">
    <div class="wordmark"><span class="wordmark__dot"></span>Kjelvraket</div>
    <div class="website">www.fjordlast.no</div>
  </section>

  <section class="card card--blue" aria-label="Visittkort bakside, blå">
    <div class="wordmark"><span class="wordmark__dot"></span>Kjelvraket</div>
    <div class="website">www.fjordlast.no</div>
  </section>

</body>
</html>
```